Anzeigengestaltung für Reinigungsunternehmen
Zielgruppe
Wir sind ein Reinigungsunternehmen mit den Haupttätigkeitsfeldern: Büroreinigung, Treppenhausreinigung und Bauendreinigung.
Webseite: www.kolbrapflege.de
Die Zielgruppe sind Unternehmer (überwiegend Büros), Hausverwaltungen sowie Bauherren.
Aufgabenstellung
Die Reinigungsfirma wird mit dieser Anzeige zum ersten Mal beworben.
Umkreis: Kreis Paderborn und Kreis Gütersloh
Die Anzeige soll sowohl in Facebook beworben werden, sowie auch in den örtlichen Rundschauen.

```html
<!DOCTYPE html>
<html lang="de">
<head>
<meta charset="utf-8">
<title>Kolbra Pflege – Banner</title>
<link rel="stylesheet" href="https://fonts.googleapis.com/css2?family=Open+Sans:wght@400;700&family=Gochi+Hand&display=swap">
<style>
  :root {
    --page-bg: #dcdcdc;
    --blue-light: #2c7dc0;
    --blue-deep: #0a66b1;
    --white: #ffffff;
    --photo-light: #e9edf1;
    --photo-mid: #c9d3dc;
    --photo-blue: #3a5aa8;
    --photo-yellow: #e6df7a;
  }
  * { margin: 0; padding: 0; box-sizing: border-box; }
  html, body {
    width: 1200px; height: 864px; overflow: hidden;
    background: var(--page-bg);
  }
  .banner {
    position: absolute; left: 0; top: 132px;
    width: 1200px; height: 600px; overflow: hidden;
    background: linear-gradient(160deg, var(--blue-light) 0%, var(--blue-deep) 75%);
    font-family: "Open Sans", sans-serif; color: var(--white);
  }
  .photo-area { position: absolute; left: 0; top: 0; }
  .brand {
    position: absolute; left: 205px; top: 42px;
    display: flex; align-items: center; gap: 16px;
  }
  .brand-mark { width: 58px; height: 58px; background: var(--white); }
  .brand-text { display: flex; flex-direction: column; }
  .brand-name { font-size: 34px; font-weight: 700; line-height: 1.05; }
  .brand-owner { font-size: 13px; font-weight: 400; margin-top: 4px; }
  .headline {
    position: absolute; left: 60px; width: 600px; top: 176px;
    text-align: center; font-weight: 700; font-size: 52px; line-height: 64px;
  }
  .subline {
    position: absolute; left: 40px; width: 600px; top: 333px;
    text-align: center; font-weight: 400; font-size: 22px; line-height: 29px;
  }
  .call-to-action {
    position: absolute; left: 72px; top: 438px;
    font-family: "Gochi Hand", cursive; font-size: 24px; line-height: 26px;
    text-transform: uppercase; letter-spacing: 1px;
    transform: rotate(-5deg); text-align: center;
  }
  .cta-arrow { position: absolute; left: 248px; top: 448px; }
  .website {
    position: absolute; left: 208px; top: 500px;
    display: flex; align-items: center; gap: 10px;
    font-size: 22px;
  }
</style>
</head>
<body>
  <main class="banner">
    <svg class="photo-area" width="1200" height="600" viewBox="0 0 1200 600" role="img" aria-label="Foto: Reinigungskraft wischt ein Büro, im Vordergrund Hand mit gelbem Handschuh und Putzeimer">
      <defs>
        <linearGradient id="photoTone" x1="0" y1="0" x2="1" y2="1">
          <stop offset="0" stop-color="var(--photo-light)"/>
          <stop offset="0.55" stop-color="var(--photo-mid)"/>
          <stop offset="0.8" stop-color="var(--photo-yellow)"/>
          <stop offset="1" stop-color="var(--photo-blue)"/>
        </linearGradient>
      </defs>
      <path d="M625 0 L1200 0 L1200 600 C900 540 700 250 625 0 Z" fill="url(#photoTone)"/>
    </svg>

    <div class="brand">
      <div class="brand-mark"></div>
      <div class="brand-text">
        <span class="brand-name">Kolbra Pflege</span>
        <span class="brand-owner">Inh. Marco Albers</span>
      </div>
    </div>

    <h1 class="headline">Schenken Sie Ihrem<br>Objekt neuen Glanz!</h1>

    <p class="subline">Zuverlässige, profesionelle<br>Reinigungskräfte in Paderborn &amp; Gütersloh</p>

    <p class="call-to-action">Jetzt<br>Angebot einholen</p>
    <svg class="cta-arrow" width="64" height="56" viewBox="0 0 64 56" aria-hidden="true">
      <path d="M2 6 C30 -2 58 10 52 46" fill="none" stroke="var(--white)" stroke-width="3" stroke-linecap="round"/>
      <path d="M44 38 L52 48 L60 38" fill="none" stroke="var(--white)" stroke-width="3" stroke-linecap="round" stroke-linejoin="round"/>
    </svg>

    <div class="website">
      <svg width="52" height="52" viewBox="0 0 52 52" aria-hidden="true" fill="none" stroke="var(--white)" stroke-width="3">
        <circle cx="26" cy="26" r="23"/>
        <ellipse cx="26" cy="26" rx="10" ry="23"/>
        <line x1="26" y1="3" x2="26" y2="49"/>
        <line x1="3" y1="26" x2="49" y2="26"/>
        <line x1="7" y1="15" x2="45" y2="15"/>
        <line x1="7" y1="37" x2="45" y2="37"/>
      </svg>
      <span>www.kolbrapflege.de</span>
    </div>
  </main>
</body>
</html>
```